Catalogue Design Project

We need a catalog design for a new private university called Redwell Institute Bayshore (see website www.rwi-bs.org). The catalog should be about 30 pages maximum and will include items such as General Information, Academic schedule, department descriptions, program descriptions, course descriptions, school policies, student services, admissions, San diego Lifestyle, etc.
I will provide the text but I need a professional design with regard to page layouts. I have provided some examples.
Ok, i posted the catalog content, just missing course descriptions.
Target Market(s)
Young Professionals, Foreign Students
Industry/Entity Type
University
Look and feel
Each slider illustrates characteristics of the customer's brand and the style your logo design should communicate.

```html
<!DOCTYPE html>
<html lang="en">
<head>
<meta charset="utf-8">
<title>Academic Programs – Travel/Study Package</title>
<link rel="stylesheet" href="https://fonts.googleapis.com/css2?family=Carlito:wght@400;700&display=swap">
<style>
  :root {
    --ink: #1a1a1a;
    --navy: #1f4e79;
    --navy-dark: #163a5c;
    --rule: #7f9bb8;
    --muted: #8a8a8a;
    --paper: #ffffff;
    --parchment: #e9dcc2;
  }
  * { box-sizing: border-box; margin: 0; padding: 0; }
  html, body { width: 927px; height: 1200px; overflow: hidden; background: var(--paper); }
  body { font-family: "Carlito", "Calibri", sans-serif; color: var(--ink); position: relative; }

  .page { position: relative; width: 927px; height: 1200px; }

  .brand {
    position: absolute; left: 60px; top: 60px;
    display: flex; align-items: center; gap: 10px;
    font-size: 15px; color: var(--navy);
  }
  .brand-dot { width: 16px; height: 16px; border-radius: 50%; background: var(--navy); }

  .header-visual {
    position: absolute; right: 0; top: 0; width: 380px; height: 150px;
    background: linear-gradient(to right, rgba(255,255,255,1) 0%, rgba(233,220,194,0.55) 45%, rgba(200,180,150,0.7) 100%);
  }

  .section-title {
    position: absolute; left: 306px; top: 96px;
    font-size: 28px; letter-spacing: 0.5px; color: var(--ink);
  }
  .section-bar { position: absolute; left: 306px; top: 133px; width: 315px; height: 17px; background: var(--navy); }
  .header-rule { position: absolute; left: 0; top: 150px; width: 927px; height: 2px; background: var(--rule); }

  .topic-tab {
    position: absolute; left: 0; top: 177px; width: 429px; height: 43px;
    background: linear-gradient(to bottom, var(--navy) 0%, var(--navy-dark) 100%);
    border-radius: 0 12px 12px 0;
    color: #fff; font-size: 27px; line-height: 43px; padding-left: 76px;
  }

  .page-heading {
    position: absolute; left: 0; top: 241px; width: 927px; text-align: center;
    font-size: 25px; font-weight: 700;
  }

  .destinations-photo {
    position: absolute; left: 67px; top: 288px; width: 818px; height: 398px;
    background: linear-gradient(135deg, #c9a4c6 0%, #e6d3ea 35%, #f1e9f3 60%, #d9cde6 100%);
  }

  .body-copy {
    position: absolute; left: 80px; top: 718px; width: 803px;
    font-size: 19.5px; line-height: 35.6px; text-align: justify;
  }
  .body-copy p + p { margin-top: 0; }
  .body-copy .contact { margin-top: 35.6px; }

  .footer-rule { position: absolute; left: 0; top: 1154px; width: 927px; height: 1px; background: var(--rule); }
  .folio {
    position: absolute; right: 36px; top: 1170px;
    font-size: 12.5px; color: var(--muted); letter-spacing: 0.3px;
  }
</style>
</head>
<body>
<div class="page">
  <div class="header-visual" role="img" aria-label="Faded photo of an open book"></div>

  <div class="brand"><span class="brand-dot"></span>Redwell Institute Bayshore</div>

  <h1 class="section-title">ACADEMIC PROGRAMS</h1>
  <div class="section-bar"></div>
  <div class="header-rule"></div>

  <div class="topic-tab">TRAVEL/STUDY PACKAGE</div>

  <h2 class="page-heading">Travel/Study Package for American Students</h2>

  <div class="destinations-photo" role="img" aria-label="City map with a handshake over soft clouds and fifteen round country flags"></div>

  <div class="body-copy">
    <p>With partnerships across 15 different countries, RWIB offers local students the opportunity of a lifetime to study, work, and travel to the destination of their choice for a short or long-term stay.</p>
    <p>Ideal for business professionals wanting to advance their careers by acquiring a foreign language while at the same time, enjoying a new life and being exposed to a new culture. Countries include Brazil, Argentina, Chile, Costa Rica, Mexico, China, Taiwan, Japan, South Korea, Vietnam, Thailand, Spain, Portugal, Turkey and Italy. &nbsp;Most packages include round-trip airfare, housing, and class enrollment; some include job placement.</p>
    <p class="contact">Please contact the university for more details.</p>
  </div>

  <div class="footer-rule"></div>
  <div class="folio">16::: REDWELL INSTITUTE</div>
</div>
</body>
</html>
```